Valdo Capital

We need a corporate style website design for a new company based in Shenzhen's Qianhai Special Economic Development Zone, China. We provide a range of financial services to large international investment companies. Typically these companies invest over 5 million RMB. The company is part of a group that consists of NorthKilns, ValdoTrusts and ValdoEquity. Our location and gateway into Qianhai Special Economic Zone is our core advantage. We would like to see designs that Do Not use purple and orange. The website design should be similar to other websites in this family but different enough to give it a unique style (See attached website links for reference). The final design should communicate financial safety and growth. This website will act partly as a business chamber with connections to the government so we would like it to be diplomatic in style.

www.northkilns.example
www.valdotrusts.example

*Nevegation Bar
Should including Homepage, Financial Product, Team, News.
Could refer to www.valdotrusts.example

*Contact Details

Miss Lan
Address:E 728, North Block, KMO Centre, East Sector, Shenzhen Bright Science Campus
Telephone: +86 0755 63920417
Cellphone: +86 13957280316

* Social Media
Should be grouped like:
1. Weibo QRcode+ Weibo
2. Social link one, Social link two, Social link three.

Industry/Entity Type

Investment

```html
<!DOCTYPE html>
<html lang="en">
<head>
<meta charset="utf-8">
<title>Valdo Capital</title>
<link rel="stylesheet" href="https://fonts.googleapis.com/css2?family=Open+Sans:wght@300;400;600;700&family=Raleway:wght@300;400&family=Cinzel:wght@500&family=Noto+Serif+SC:wght@400&display=swap">
<style>
:root{
  --ink:#333a40;
  --muted:#8a8f94;
  --soft:#b4b8bc;
  --accent:#6a9ed6;
  --accent-dark:#4d82bd;
  --sky:#3bb0e0;
  --panel:#f4f4f4;
  --rule:#dcdcdc;
  --footer:#101112;
  --white:#ffffff;
}
*{box-sizing:border-box;margin:0;padding:0}
html,body{width:831px;height:1200px;overflow:hidden;background:var(--white)}
body{position:relative;font-family:'Open Sans',sans-serif;color:var(--ink)}
.abs{position:absolute}

/* hero */
.hero{left:0;top:0;width:831px;height:501px;
  background:
   radial-gradient(ellipse at 70% 75%,rgba(230,160,70,.55),transparent 45%),
   radial-gradient(ellipse at 85% 40%,rgba(240,190,110,.35),transparent 35%),
   linear-gradient(180deg,#1d3050 0%,#2d4e78 35%,#27446a 60%,#1a2a40 100%);}
.brand{left:76px;top:14px;display:flex;align-items:center;gap:9px}
.brand-dot{width:40px;height:40px;border-radius:50%;background:#2c6a9a}
.brand-name{font-family:'Cinzel',serif;font-size:19px;color:var(--white);letter-spacing:.5px;line-height:1}
.brand-sub{font-family:'Noto Serif SC',serif;font-size:9px;color:var(--white);margin-top:4px;letter-spacing:1px}
.topbar{left:594px;top:16px;font-size:10px;color:#dfe6ee}
.topbar u{margin-right:2px}
.topbar .phone{margin-left:22px;font-size:11px}
.nav{top:45px;right:76px;display:flex;gap:23px;font-size:9.5px;color:#dfe6ee}
.nav .current{color:var(--white);font-weight:600}
.hero-welcome{left:78px;top:160px;font-family:'Raleway',sans-serif;font-weight:300;font-size:42px;color:#1a1f26;letter-spacing:-1px}
.hero-title{left:79px;top:202px;font-weight:600;font-size:44px;color:var(--white);letter-spacing:-.5px}
.hero-text{left:82px;top:257px;width:325px;font-size:12.5px;line-height:15.5px;color:var(--white)}
.hero-link{left:82px;top:308px;font-size:12px;color:var(--white);text-decoration:underline}
.hero-link span{font-size:7px;text-decoration:none;margin-left:3px}

/* services */
.service-icon{width:53px;height:53px;border-radius:50%;background:var(--accent);display:flex;align-items:center;justify-content:center}
.service-title{font-family:'Raleway',sans-serif;font-size:11.5px;color:#333;letter-spacing:.2px}
.service-text{width:140px;font-family:'Raleway',sans-serif;font-size:9.5px;line-height:15px;color:#444}
.btn{width:69px;height:20px;background:var(--accent);border-bottom:2px solid var(--accent-dark);border-right:1px solid var(--accent-dark);color:var(--white);font-size:9.5px;display:flex;align-items:center;justify-content:center}

/* posts & testimonials */
.panel{left:0;top:679px;width:831px;height:213px;background:var(--panel);border-bottom:2px solid var(--rule)}
.section-head{font-size:11.5px;font-weight:600;color:#333;letter-spacing:.2px}
.head-rule{height:2px;background:#e6e6e6}
.pager{display:flex;gap:4px}
.pager i{width:13px;height:13px;background:var(--sky);display:block;opacity:.85}
.post-photo{left:81px;top:739px;width:177px;height:118px;background:linear-gradient(120deg,#d9d9d6 0%,#c7a57f 55%,#a3683e 100%)}
.post-title{left:268px;top:739px;font-size:12px;color:#444}
.post-meta{left:268px;top:768px;width:168px;font-size:7px;line-height:13px;color:var(--soft);border-top:1px solid #e6e6e6;border-bottom:1px solid #e6e6e6;padding:3px 0 4px}
.post-meta b{font-weight:600;color:#a9adb1}
.post-body{left:268px;top:805px;width:170px;font-size:10px;line-height:13.5px;color:#333}
.quote{left:577px;top:732px;width:160px;font-size:10px;line-height:14px;color:#333}
.quote a{font-size:7px;color:var(--sky);font-weight:600;text-decoration:none}
.avatar{left:577px;top:795px;width:44px;height:44px;border-radius:50%;background:#8a7a6c}
.person{left:632px;top:794px;font-size:11.5px;color:#444}
.role{left:632px;top:813px;font-size:7.5px;color:#555}

/* clients */
.clients-title{left:0;top:918px;width:831px;text-align:center;font-family:'Raleway',sans-serif;font-weight:300;font-size:22px;color:#8a8f94}
.clients-title span{color:var(--sky)}
.clients-text{left:110px;top:955px;width:611px;text-align:center;font-family:'Raleway',sans-serif;font-weight:300;font-size:12px;line-height:20px;color:var(--muted)}
.client{top:1060px;font-size:17px;font-weight:700;color:#555;display:flex;align-items:center;gap:7px}
.client i{width:14px;height:14px;border-radius:50%;background:#777;display:block}

/* footer */
.footer{left:0;top:1138px;width:831px;height:62px;background:var(--footer)}
.footer .brand{top:8px}
.footer .brand-dot{background:#3a3d40}
.footer .brand-name,.footer .brand-sub{color:#9da1a5}
.copyright{left:284px;top:1165px;font-size:9px;color:#a9adb1}
.follow{left:686px;top:1149px;font-size:12px;color:var(--white)}
.social{top:1167px;width:21px;height:21px;border-radius:50%;background:#3a3c3e}
</style>
</head>
<body>

<div class="abs hero" role="img" aria-label="Night view of a harbour city skyline with lit towers and waterfront"></div>

<div class="abs brand">
  <span class="brand-dot"></span>
  <div>
    <div class="brand-name">VALDO CAPITAL</div>
    <div class="brand-sub">深圳前海瓦铎资本控股有限公司</div>
  </div>
</div>
<div class="abs topbar"><u>EN</u> | SP ▾ <span class="phone">☐ +86 0755 63920417</span></div>
<nav class="abs nav">
  <span class="current">HOME</span><span>FINANCIAL PRODUCTS</span><span>TEAM</span><span>NEWS</span>
</nav>

<div class="abs hero-welcome">Welcome To</div>
<div class="abs hero-title">Valdo Capital</div>
<p class="abs hero-text">Lorem ipsum dolor sit amet, consectetur adipisicing elit, sed do eiusmod tempor incididunt ut labore et dolore magna aliqua..</p>
<div class="abs hero-link">Read More<span>▸</span></div>

<!-- services -->
<div class="abs service-icon" style="left:77px;top:533px">
  <svg width="22" height="18" viewBox="0 0 22 18"><rect x="1" y="4" width="20" height="13" rx="2" fill="#fff"/><rect x="7" y="1" width="8" height="4" rx="1" fill="none" stroke="#fff" stroke-width="1.6"/><rect x="9" y="9" width="4" height="3" fill="#6a9ed6"/></svg>
</div>
<div class="abs service-title" style="left:148px;top:537px">DOCUMENTS</div>
<p class="abs service-text" style="left:149px;top:555px">Sed ut perspiciatis unde omnis iste natus error sit voluptatem</p>
<div class="abs btn" style="left:149px;top:593px">Read More</div>

<div class="abs service-icon" style="left:308px;top:534px">
  <svg width="26" height="22" viewBox="0 0 26 22"><ellipse cx="10" cy="9" rx="9" ry="7" fill="none" stroke="#fff" stroke-width="1.5"/><ellipse cx="16" cy="12" rx="8" ry="6" fill="#fff"/><circle cx="13" cy="12" r="1" fill="#6a9ed6"/><circle cx="16" cy="12" r="1" fill="#6a9ed6"/><circle cx="19" cy="12" r="1" fill="#6a9ed6"/></svg>
</div>
<div class="abs service-title" style="left:380px;top:536px">GET A QUOTE</div>
<p class="abs service-text" style="left:380px;top:556px">Sed ut perspiciatis unde omnis iste natus error sit voluptatem</p>
<div class="abs btn" style="left:380px;top:593px">Read More</div>

<div class="abs service-icon" style="left:547px;top:536px">
  <svg width="22" height="20" viewBox="0 0 22 20"><path d="M1 9 L21 1 L14 19 L11 11 Z" fill="#fff"/></svg>
</div>
<div class="abs service-title" style="left:609px;top:536px">PRINT LIST OF RECIPIENTS</div>
<p class="abs service-text" style="left:611px;top:553px">Sed ut perspiciatis unde omnis iste natus error sit voluptatem</p>
<div class="abs btn" style="left:610px;top:593px">Read More</div>

<!-- posts & testimonials -->
<div class="abs panel"></div>
<div class="abs section-head" style="left:81px;top:695px">RECENT POSTS</div>
<div class="abs pager" style="left:408px;top:696px"><i></i><i></i><i></i></div>
<div class="abs head-rule" style="left:81px;top:715px;width:374px"></div>
<div class="abs post-photo" role="img" aria-label="Desk with laptop, notebooks and printed design samples"></div>
<div class="abs post-title">Another Post with Everything</div>
<div class="abs post-meta">SEPTEMBER 17,2008 / <b>GENERAL NEWS<br>TECHNOLOGY</b> / 3 COMMENTS</div>
<p class="abs post-body">Lorem ipsum dolor sit amet, consectetuer adipiscing elit. Curabitur quam augue, vehicula quis....</p>

<div class="abs section-head" style="left:577px;top:695px">TESTIMONIALS</div>
<div class="abs pager" style="left:725px;top:697px"><i></i><i></i></div>
<div class="abs head-rule" style="left:577px;top:715px;width:177px"></div>
<p class="abs quote">There are many variations of passages of Lorem Ipsum available, but the majority have suffered...<a>READ MORE</a></p>
<div class="abs avatar" role="img" aria-label="Portrait of the reviewer"></div>
<div class="abs person">Marla Quinton</div>
<div class="abs role">Designer</div>

<!-- clients -->
<h2 class="abs clients-title">Our <span>Clients</span></h2>
<p class="abs clients-text">Lorem ipsum dolor sit amet, consectetur adipiscing elit. Fusceelementum, nulla vel pellentesque consequat, ante nulla hendrerit arcu, ac tincidunt mauris lacus sed leo. vamus suscipit molestie vestibulum. Integer elementum congue.</p>
<div class="abs client" style="left:76px"><i></i>Harbor Nine</div>
<div class="abs client" style="left:228px">Oakline</div>
<div class="abs client" style="left:350px"><i></i>Meridia</div>
<div class="abs client" style="left:495px">Tesselwork</div>
<div class="abs client" style="left:690px">Corvan</div>

<!-- footer -->
<footer class="abs footer">
  <div class="abs brand">
    <span class="brand-dot"></span>
    <div>
      <div class="brand-name">VALDO CAPITAL</div>
      <div class="brand-sub">深圳前海瓦铎资本控股有限公司</div>
    </div>
  </div>
</footer>
<div class="abs copyright">© Copyright 2014 by Valdo Capital. All Rights Reserved.</div>
<div class="abs follow">Follow Us</div>
<span class="abs social" style="left:682px" aria-label="Social link one"></span>
<span class="abs social" style="left:708px" aria-label="Social link two"></span>
<span class="abs social" style="left:733px" aria-label="Social link three"></span>

</body>
</html>
```